Website for Apartment Rental in Prague

I would like to create designs of my website focused on luxury apartment rentals in Prague, Czech Republic. I created initial mock-ups, They are all attached. I need to design homepage and subpage. The mock-ups were created by combining elements from different websites that I liked but I need you to create a design that is unique and original. The attached files a only a guidance for the structure of the website but not for the design. Try to be creative.

Apartment

```html
<!DOCTYPE html>
<html lang="en">
<head>
<meta charset="utf-8">
<title>Velour Residences Prague</title>
<link href="https://fonts.googleapis.com/css2?family=Lato:wght@400;700&family=Noto+Serif:ital,wght@0,400;1,400;1,700&display=swap" rel="stylesheet">
<style>
:root{
  --ink:#222222;
  --dark:#1f1f1f;
  --text:#555555;
  --muted:#777777;
  --gold:#bfaf7c;
  --gold-deep:#a89460;
  --light:#f3f3f3;
  --line:#e6e6e6;
  --white:#ffffff;
}
*{box-sizing:border-box;margin:0;padding:0}
html,body{width:1200px;height:2965px;overflow:hidden}
body{position:relative;font-family:"Lato",Arial,sans-serif;color:var(--text);background:var(--white)}
.abs{position:absolute}

.topbar{left:0;top:0;width:1200px;height:28px;background:var(--ink);color:#ddd;font-size:12px;display:flex;justify-content:center;align-items:center;gap:34px}
.topbar span{display:flex;align-items:center;gap:7px}
.topbar svg{width:12px;height:12px}

.header{left:0;top:28px;width:1200px;height:107px;background:var(--white)}
.brand{left:112px;top:26px;width:130px;text-align:center;color:var(--ink);font-size:15px;font-weight:700;letter-spacing:3px;line-height:20px}
.nav{right:90px;top:48px;display:flex;gap:32px;font-size:14px;color:#444}
.nav .active{color:var(--gold-deep)}

.ribbon{left:0;top:135px;width:1200px;height:39px;background:var(--gold);color:var(--white);font-size:16px;letter-spacing:3px;text-align:center;line-height:39px}

.hero{left:0;top:174px;width:1200px;height:514px;background:linear-gradient(100deg,#2f2f33 0%,#4b4844 35%,#6b655c 60%,#3a3b3e 100%)}
.hero-title{left:0;top:450px;width:1200px;text-align:center;color:var(--white);font-size:38px;font-weight:700;letter-spacing:0.5px}
.booking{left:119px;top:180px;width:964px;height:82px;background:rgba(255,255,255,0.93)}
.field{position:absolute;top:8px;font-size:11px;color:#888}
.field .box{margin-top:7px;height:34px;border:1px solid #ccc;background:var(--white);font-size:12px;color:#444;line-height:32px;padding-left:10px}
.check{position:absolute;left:621px;top:29px;width:150px;height:36px;background:var(--gold);color:var(--white);font-size:12px;font-weight:700;text-align:center;line-height:36px}
.or{position:absolute;left:781px;top:29px;line-height:36px;font-size:13px;color:#444}
.unit{position:absolute;left:806px;top:29px;width:146px;height:36px;border:1px solid #ccc;background:var(--white);font-size:12px;color:#555;line-height:34px;padding-left:10px}

.vision{left:0;top:688px;width:1200px;height:601px;background:linear-gradient(160deg,#f7f7f7 0%,#eeeeee 50%,#f9f9f9 100%)}
.vision .kicker{position:absolute;top:66px;width:100%;text-align:center;font-size:24px;letter-spacing:5px;color:#333}
.vision .title{position:absolute;top:96px;width:100%;text-align:center;font-family:"Noto Serif",Georgia,serif;font-style:italic;font-weight:700;font-size:44px;color:var(--gold-deep)}
.serif-copy{position:absolute;width:100%;text-align:center;font-family:"Noto Serif",Georgia,serif;font-style:italic;font-size:15px;line-height:24px;color:#555}
.divider{position:absolute;top:308px;left:445px;width:310px;height:52px}
.vision .sub{position:absolute;top:370px;width:100%;text-align:center;font-size:16px;color:#333;line-height:26px}
.vision .body{position:absolute;top:447px;left:110px;width:980px;text-align:center;font-size:13.5px;line-height:25px;color:#666}

.cards{left:0;top:1289px;width:1200px;height:1083px;background:var(--white)}
.card{position:absolute;width:308px}
.card h3{height:50px;text-align:center;font-size:16px;font-weight:700;color:#222;line-height:24px}
.photo{position:relative;height:226px}
.price{position:absolute;left:0;top:38px;background:var(--white);padding:5px 10px;font-size:13px;color:#444}
.price b{color:#222}
.meta{height:32px;background:#ececec;display:flex;font-size:12.5px;color:#333;line-height:32px}
.meta span{flex:1;text-align:center}
.teaser{height:55px;text-align:center;font-size:13.5px;color:#777;line-height:55px}
.btn{height:34px;text-align:center;line-height:34px;font-size:13px;font-weight:700;color:var(--white);margin-bottom:8px}
.btn-dark{background:var(--dark)}
.btn-gold{background:var(--gold)}

.know{left:0;top:2372px;width:1200px;height:338px;background:linear-gradient(135deg,#f1f1f1 0%,#f7f7f7 50%,#eeeeee 100%)}
.know h2{position:absolute;top:58px;width:100%;text-align:center;font-size:24px;font-weight:400;letter-spacing:5px;color:#333}
.fact{position:absolute;top:140px;width:330px;text-align:center}
.fact svg{width:60px;height:60px}
.fact h4{margin-top:8px;font-size:16px;font-weight:700;color:#333}
.fact p{margin-top:10px;font-size:13.5px;line-height:24px;color:#666}

.footer{left:0;top:2710px;width:1200px;height:255px;background:var(--ink);color:#ddd}
.footer h5{font-size:17px;font-weight:400;color:var(--white);margin-bottom:14px}
.col{position:absolute;top:42px}
.col p{font-size:12px;line-height:19px;color:#ccc}
.phone{font-size:26px;color:var(--white);margin-top:24px}
.links{display:grid;grid-template-columns:118px 160px;font-size:12px;line-height:26px;color:#ccc}
.socials{display:flex;gap:6px}
.socials i{width:32px;height:32px;border:2px solid #bbb;border-radius:50%;display:block}
.message{left:864px;top:2922px;width:223px;height:43px;background:var(--gold);color:var(--white);font-size:14px;font-weight:700;line-height:43px;text-align:center;border-radius:5px 5px 0 0}
</style>
</head>
<body>

<div class="abs topbar">
  <span><svg viewBox="0 0 12 12"><circle cx="6" cy="6" r="5" fill="none" stroke="#ccc"/></svg>Our Hospitality</span>
  <span><svg viewBox="0 0 12 12"><path d="M6 11C3 7 2 5.5 2 4a4 4 0 0 1 8 0c0 1.5-1 3-4 7z" fill="#ccc"/></svg>Discover Prague</span>
  <span><svg viewBox="0 0 12 12"><rect x="1" y="3" width="10" height="7" fill="none" stroke="#ccc"/><path d="M1 3l5 4 5-4" fill="none" stroke="#ccc"/></svg>reservation@velourstays.com</span>
  <span><svg viewBox="0 0 12 12"><path d="M3 1l2 3-1 1.5c.7 1.5 1.5 2.3 3 3L8.5 7l3 2-1.5 2C5 11 1 7 1 2.5z" fill="#ccc"/></svg>420 600 318 442</span>
  <span>En ▾</span>
</div>

<div class="abs header">
  <div class="abs brand">VELOUR<br>RESIDENCES<br>PRAGUE</div>
  <nav class="abs nav">
    <span class="active">Apartments</span><span>Location</span><span>Services</span><span>Gallery</span><span>News</span><span>Exclusive Offers &amp; Tours</span><span>For Families</span><span>Contact</span>
  </nav>
</div>

<div class="abs ribbon">OFFICIAL SITE - BEST PRICE GUARANTEED</div>

<div class="abs hero" role="img" aria-label="Photo of a dark modern living room with leather sofa and dining area"></div>
<div class="abs hero-title">BEING HOME IN PRAGUE</div>

<form class="abs booking">
  <div class="field" style="left:10px;width:120px">Check in date<div class="box">11/17/2017</div></div>
  <div class="field" style="left:138px;width:120px">Check out date<div class="box">11/18/2017</div></div>
  <div class="field" style="left:266px;width:48px">Adults<div class="box">2</div></div>
  <div class="field" style="left:322px;width:48px">Children<div class="box">0</div></div>
  <div class="field" style="left:378px;width:48px">Infants<div class="box">0</div></div>
  <div class="field" style="left:434px;width:176px">Promotional code<div class="box"></div></div>
  <div class="check">CHECK AVAILABILITY</div>
  <div class="or">OR</div>
  <div class="unit">Select Rental Unit ▾</div>
</form>

<section class="abs vision">
  <div class="kicker">A DIFFERENT VISION OF</div>
  <div class="title">Travelling</div>
  <p class="serif-copy" style="top:178px">Something spectacular has arrived in the heart of europe.</p>
  <p class="serif-copy" style="top:228px;left:110px;width:980px">Steps from old town, this rental experience is curated with world-class amenities, exemplary style and a level of convenience you have to experience to believe. Experience the different vision of luxury in center of prague.</p>
  <svg class="divider" viewBox="0 0 310 52">
    <line x1="0" y1="26" x2="127" y2="26" stroke="#bfaf7c" stroke-width="1.5"/>
    <line x1="183" y1="26" x2="310" y2="26" stroke="#bfaf7c" stroke-width="1.5"/>
    <circle cx="155" cy="26" r="25" fill="none" stroke="#bfaf7c" stroke-width="1.5"/>
    <path d="M147 15h16l-3 12h-10z M155 27v10 M149 37h12" fill="none" stroke="#bfaf7c" stroke-width="1.5"/>
  </svg>
  <div class="sub">Interiors Designed<br><span style="color:#777">by Velour</span></div>
  <p class="body">Velour apartments offers short term and as well as long term options in our studio apartments and our one bedroom apartment homes. Our luxurious apartments and high quality customer service have allowed us to dominate the Prague apartment market with a proven track record. Our years of experience and knowledge have made us a premier apartment rental company as we continue to stress the importance of servicing individuals and corporations who are seeking the finest accommodations.</p>
</section>

<section class="abs cards">
  <article class="card" style="left:111px;top:71px">
    <h3>Brand New Luxury Living<br>Stunning Contemporary Design</h3>
    <div class="photo" role="img" aria-label="Photo of a bright open-plan living room with wooden floor" style="background:linear-gradient(135deg,#e8e2d8,#a87a52)"><span class="price"><i>From</i> <b>150 USD</b></span></div>
    <div class="meta"><span>1 Bedroom</span><span>Max 4 People</span></div>
    <div class="teaser">The 22nd issue is dedicated to colors...</div>
    <div class="btn btn-dark">DETAILS</div><div class="btn btn-gold">BOOK NOW</div>
  </article>
  <article class="card" style="left:445px;top:71px">
    <h3>Brand New Luxury Living<br>Stunning Contemporary Design</h3>
    <div class="photo" role="img" aria-label="Photo of a living room with tall windows and a red rug" style="background:linear-gradient(135deg,#d9d4cc,#8a6f66)"><span class="price"><i>From</i> <b>150 USD</b></span></div>
    <div class="meta"><span>1 Bedroom</span><span>Max 4 People</span></div>
    <div class="teaser">The 22nd issue is dedicated to colors...</div>
    <div class="btn btn-dark">DETAILS</div><div class="btn btn-gold">BOOK NOW</div>
  </article>
  <article class="card" style="left:779px;top:71px">
    <h3>Brand New Luxury Living<br>Stunning Contemporary Design</h3>
    <div class="photo" role="img" aria-label="Photo of a warmly lit bedroom at night" style="background:linear-gradient(135deg,#5a3a22,#c9934f)"><span class="price"><i>From</i> <b>150 USD</b></span></div>
    <div class="meta"><span>1 Bedroom</span><span>Max 4 People</span></div>
    <div class="teaser">The 22nd issue is dedicated to colors...</div>
    <div class="btn btn-dark">DETAILS</div><div class="btn btn-gold">BOOK NOW</div>
  </article>
  <article class="card" style="left:111px;top:569px">
    <h3>Brand New Luxury Living<br>Stunning Contemporary Design</h3>
    <div class="photo" role="img" aria-label="Photo of a modern lounge with green wall accent" style="background:linear-gradient(135deg,#e6e0d2,#9b8a5e)"><span class="price"><i>From</i> <b>150 USD</b></span></div>
    <div class="meta"><span>1 Bedroom</span><span>Max 4 People</span></div>
    <div class="teaser">The 22nd issue is dedicated to colors...</div>
    <div class="btn btn-dark">DETAILS</div><div class="btn btn-gold">BOOK NOW</div>
  </article>
  <article class="card" style="left:445px;top:569px">
    <h3>Brand New Luxury Living<br>Stunning Contemporary Design</h3>
    <div class="photo" role="img" aria-label="Photo of a duplex interior with open staircase" style="background:linear-gradient(135deg,#f0e6d2,#b98a4e)"><span class="price"><i>From</i> <b>150 USD</b></span></div>
    <div class="meta"><span>1 Bedroom</span><span>Max 4 People</span></div>
    <div class="teaser">The 22nd issue is dedicated to colors...</div>
    <div class="btn btn-dark">DETAILS</div><div class="btn btn-gold">BOOK NOW</div>
  </article>
  <article class="card" style="left:779px;top:569px">
    <h3>Brand New Luxury Living<br>Stunning Contemporary Design</h3>
    <div class="photo" role="img" aria-label="Photo of a living room with blue sofa and wooden floor" style="background:linear-gradient(135deg,#7d7468,#b48a5c)"><span class="price"><i>From</i> <b>150 USD</b></span></div>
    <div class="meta"><span>1 Bedroom</span><span>Max 4 People</span></div>
    <div class="teaser">The 22nd issue is dedicated to colors...</div>
    <div class="btn btn-dark">DETAILS</div><div class="btn btn-gold">BOOK NOW</div>
  </article>
</section>

<section class="abs know">
  <h2>NEED TO KNOW</h2>
  <div class="fact" style="left:100px">
    <svg viewBox="0 0 60 60" fill="none" stroke="#bfaf7c" stroke-width="2"><rect x="14" y="14" width="20" height="38"/><rect x="34" y="26" width="14" height="26"/><path d="M19 20h4M26 20h4M19 28h4M26 28h4M19 36h4M26 36h4M38 32h6M38 40h6"/><path d="M10 52h42"/></svg>
    <h4>Apartments</h4>
    <p>Also available to rent all the apartmets<br>together for companies or larger groups.</p>
  </div>
  <div class="fact" style="left:434px">
    <svg viewBox="0 0 60 60" fill="none" stroke="#bfaf7c" stroke-width="2"><rect x="14" y="20" width="32" height="30" rx="3"/><path d="M24 20v-8h12v8M22 26v18M30 26v18M38 26v18M18 50v4M42 50v4"/></svg>
    <h4>Check-Out</h4>
    <p>12 noon; earliest check-in, 3pm- both are<br>flexible, by arrangement.</p>
  </div>
  <div class="fact" style="left:768px">
    <svg viewBox="0 0 60 60" fill="none" stroke="#bfaf7c" stroke-width="2"><circle cx="30" cy="30" r="22"/><path d="M37 22c-2-3-12-4-13 1s13 4 13 10-11 5-14 1M30 15v30"/></svg>
    <h4>Rates</h4>
    <p>Prices from <b style="color:#333">150 USD</b> per night.<br>Including tax.</p>
  </div>
</section>

<footer class="abs footer">
  <div class="col" style="left:111px">
    <h5>Contact Us</h5>
    <p>Velour Residences Prague<br>228, lorem ipsum dolor sit,<br>osis amet it 85965</p>
    <div class="phone">420 600 318 442</div>
    <p>reservation@velourstays.com</p>
  </div>
  <div class="col" style="left:445px">
    <h5>Quick Links</h5>
    <div class="links">
      <span>Apartments</span><span>Exclusive Offers &amp; Tours</span>
      <span>Location</span><span>For Families</span>
      <span>Services</span><span>Contact Us</span>
      <span>Gallery</span><span></span>
      <span>News</span><span></span>
    </div>
  </div>
  <div class="col" style="left:862px">
    <h5>Stay Connected</h5>
    <div class="socials"><i></i><i></i><i></i><i></i><i></i></div>
    <p style="margin-top:16px">© 2017 Velour Residences Prague.</p>
  </div>
</footer>
<div class="abs message">Please Leave A Message</div>

</body>
</html>
```